New Patient Pamphlet

We need a pamphlet designed to attract new patients to our clinic.. We would like it to mention the different types of languages that are spoken at the clinic as well as it being a new patient promotional pack for $195 for exam, clean, fluoride and x-rays. The languages spoken at the clinic are: English, Hindi, Punjabi and Persian.
Please see link below to website so you are able to also add the our services that we provide on the pamphlet that are listed on the website.
https://www.brookvaledental.com/

```html
<!DOCTYPE html>
<html lang="en">
<head>
<meta charset="utf-8">
<title>Brookvale Dental – New Patient Pamphlet</title>
<link rel="stylesheet" href="https://fonts.googleapis.com/css2?family=Lato:ital,wght@0,400;0,700;0,900;1,700;1,900&display=swap">
<style>
  :root {
    --navy: #1f3f94;
    --brand-blue: #1d3c8f;
    --green: #3aa54a;
    --green-light: #8cc63f;
    --paper: #eef0f3;
    --white: #ffffff;
    --ink: #2a2a2a;
  }
  * { margin: 0; padding: 0; box-sizing: border-box; }
  html, body { width: 960px; height: 1200px; overflow: hidden; }
  body { font-family: "Lato", Arial, sans-serif; background: var(--paper); }
  .pamphlet { position: relative; width: 960px; height: 1200px; overflow: hidden; background: var(--paper); }
  .backdrop { position: absolute; inset: 0; }

  .brand { position: absolute; left: 82px; top: 84px; width: 350px; text-align: center; }
  .brand-name { display: flex; align-items: center; justify-content: center; gap: 10px;
    font-weight: 700; font-size: 38px; color: var(--brand-blue); }
  .brand-dot { width: 16px; height: 16px; border-radius: 50%; background: var(--green); }
  .brand-tagline { margin-top: 14px; border-top: 1.5px solid var(--green); padding-top: 8px;
    font-size: 15px; letter-spacing: 7px; color: var(--green); font-weight: 400; }

  .offer { position: absolute; left: 62px; width: 450px; text-align: center; color: var(--white); font-style: italic; font-weight: 900; }
  .offer-welcome { top: 258px; font-size: 32px; }
  .offer-name { top: 296px; font-size: 43px; }
  .offer-rule { position: absolute; left: 142px; top: 358px; width: 290px; height: 2px; background: rgba(255,255,255,.55); }
  .offer-lead { top: 372px; font-size: 31px; font-weight: 700; }
  .offer-pack { top: 412px; font-size: 23px; font-weight: 700; }
  .offer-price { top: 456px; font-size: 24px; font-weight: 700; }
  .offer-price strong { font-size: 44px; font-weight: 900; vertical-align: -3px; }
  .offer-items { top: 514px; font-size: 23px; font-weight: 700; }

  .categories { position: absolute; top: 700px; left: 0; width: 960px; }
  .category { position: absolute; border-left: 3px solid var(--green-light); padding-left: 11px;
    color: var(--white); font-size: 20px; font-weight: 700; line-height: 1.3; }

  .services-title { position: absolute; left: 240px; top: 772px; width: 520px; text-align: center;
    color: var(--white); font-size: 27px; font-weight: 700; }

  .service-list { position: absolute; top: 846px; list-style: none; color: var(--white); font-size: 18px; line-height: 22px; white-space: nowrap; }
  .service-list li { position: relative; padding-left: 20px; margin-bottom: 8px; }
  .service-list li::before { content: ""; position: absolute; left: 0; top: 5px; width: 13px; height: 13px;
    border: 1.5px solid var(--green-light); border-radius: 50%; }
  .service-list li::after { content: ""; position: absolute; left: 4.5px; top: 7.5px; width: 3px; height: 6px;
    border-right: 1.5px solid var(--green-light); border-bottom: 1.5px solid var(--green-light); transform: rotate(45deg); }
  .col-one { left: 70px; }
  .col-two { left: 349px; }
  .col-three { left: 652px; }

  .book-badge { position: absolute; left: 578px; top: 976px; width: 100px; height: 100px; border-radius: 50%;
    background: var(--green); border: 4px solid var(--white); display: flex; align-items: center; justify-content: center;
    text-align: center; color: var(--white); font-weight: 900; font-size: 17px; line-height: 1.05; }

  .social-dot { position: absolute; left: 855px; top: 1028px; width: 36px; height: 36px; border-radius: 50%;
    background: var(--navy); border: 3px solid var(--white); }

  .contact { position: absolute; left: 556px; top: 1084px; list-style: none; color: var(--white); font-weight: 700; font-size: 20px; }
  .contact li { display: flex; align-items: center; gap: 12px; margin-bottom: 9px; }
  .contact svg { width: 18px; height: 18px; flex: none; }

  .languages { position: absolute; left: 70px; top: 1124px; color: var(--ink); }
  .languages-intro { font-size: 16px; }
  .languages-list { font-size: 19px; font-weight: 700; margin-top: 6px; }
</style>
</head>
<body>
<main class="pamphlet">
  <svg class="backdrop" width="960" height="1200" viewBox="0 0 960 1200">
    <defs>
      <linearGradient id="toothGreen" x1="0" y1="0" x2="1" y2="1">
        <stop offset="0" stop-color="#8cc63f"/>
        <stop offset="1" stop-color="#2f9e4a"/>
      </linearGradient>
      <linearGradient id="panelGreen" x1="0" y1="1" x2="1" y2="0">
        <stop offset="0" stop-color="#2f9e4a"/>
        <stop offset="1" stop-color="#8cc63f"/>
      </linearGradient>
      <linearGradient id="photoTones" x1="0" y1="0" x2="0" y2="1">
        <stop offset="0" stop-color="#f4f4f4"/>
        <stop offset="0.45" stop-color="#e9c9b4"/>
        <stop offset="0.75" stop-color="#b9322b"/>
        <stop offset="1" stop-color="#9e1f1f"/>
      </linearGradient>
      <radialGradient id="chairGlow" cx="0.3" cy="0.4" r="0.5">
        <stop offset="0" stop-color="#3a5aa8" stop-opacity="0.8"/>
        <stop offset="1" stop-color="#1f3f94" stop-opacity="0"/>
      </radialGradient>
      <clipPath id="toothShape">
        <path d="M290 240 C240 205 130 200 95 260 C55 330 65 420 90 500 C115 580 140 645 190 645 C235 645 230 565 258 565 C290 565 300 668 370 668 C430 668 470 560 495 480 C520 400 520 300 470 250 C420 200 340 210 290 240 Z"/>
      </clipPath>
    </defs>

    <path class="blue-field" fill="var(--navy)" d="M0 425 C200 390 400 420 520 470 L960 480 L960 1060 L486 1100 C300 1090 120 1060 0 1030 Z"/>
    <rect class="chair-photo" role="img" aria-label="Faded photo of a patient in the dental chair" x="0" y="480" width="620" height="560" fill="url(#chairGlow)"/>

    <path class="photo-frame" role="img" aria-label="Photo of a smiling young woman in a red turtleneck pointing at her smile" fill="url(#photoTones)" stroke="#fff" stroke-width="6"
      d="M450 260 C450 120 560 40 700 30 L960 20 L960 631 C900 600 880 530 810 530 C740 530 700 640 600 632 C540 628 520 520 500 460 C470 400 450 330 450 260 Z"/>
    <path class="accent-arc" fill="none" stroke="var(--green-light)" stroke-width="14" d="M456 165 C520 60 640 40 760 38 C860 36 920 34 960 30"/>

    <path class="offer-tooth" fill="url(#toothGreen)" stroke="#fff" stroke-width="7"
      d="M290 240 C240 205 130 200 95 260 C55 330 65 420 90 500 C115 580 140 645 190 645 C235 645 230 565 258 565 C290 565 300 668 370 668 C430 668 470 560 495 480 C520 400 520 300 470 250 C420 200 340 210 290 240 Z"/>
    <rect class="price-band" clip-path="url(#toothShape)" x="50" y="452" width="480" height="58" fill="var(--navy)"/>

    <path class="services-frame" fill="none" stroke="#fff" stroke-width="1.5"
      d="M70 790 L255 790 Q265 790 267 800 L269 812 Q271 820 281 820 L719 820 Q729 820 731 812 L733 800 Q735 790 745 790 L890 790"/>

    <path class="contact-panel" fill="url(#panelGreen)" d="M486 1200 L486 1120 C500 1070 540 1050 600 1050 C700 1050 760 1080 840 1060 C890 1045 930 1030 960 1030 L960 1200 Z"/>
  </svg>

  <header class="brand">
    <div class="brand-name"><span class="brand-dot"></span>Brookvale Dental</div>
    <div class="brand-tagline">FAMILY DENTAL CARE</div>
  </header>

  <section class="offer-copy">
    <p class="offer offer-welcome">Welcome to</p>
    <h1 class="offer offer-name">Brookvale Dental</h1>
    <span class="offer-rule"></span>
    <p class="offer offer-lead">being a new patient</p>
    <p class="offer offer-pack">promotional pack</p>
    <p class="offer offer-price">for <strong>$195</strong> for exam</p>
    <p class="offer offer-items">clean, fluoride and x-rays.</p>
  </section>

  <nav class="categories">
    <div class="category" style="left:73px">General<br>Dentistry</div>
    <div class="category" style="left:238px">Cosmetic<br>Dentistry</div>
    <div class="category" style="left:405px">Payment<br>Plans</div>
    <div class="category" style="left:569px">Teeth<br>Straightening</div>
    <div class="category" style="left:774px">Teeth<br>Whitening</div>
  </nav>

  <h2 class="services-title">We Offer a Wide Range of Services</h2>

  <ul class="service-list col-one">
    <li>Amalgam Replacement</li>
    <li>Dentures</li>
    <li>Gum Treatment</li>
    <li>Help for headaches/jaw<br>pain (TMJ disorders)</li>
    <li>Cosmetic Dentistry</li>
    <li>Teeth Straightening</li>
  </ul>
  <ul class="service-list col-two">
    <li>Laser treatment for<br>tongue tie</li>
    <li>Implants</li>
    <li>Porcelain crowns</li>
    <li>Root canal treatment</li>
    <li>Sedation</li>
    <li>Specialised dentistry</li>
  </ul>
  <ul class="service-list col-three">
    <li>Tooth replacement</li>
    <li>Veneers</li>
    <li>Wisdom teeth removal</li>
    <li>White fillings and onlays</li>
    <li>Express in-chair teeth<br>whitening</li>
  </ul>

  <div class="book-badge">BOOK<br>ONLINE</div>
  <span class="social-dot"></span>

  <ul class="contact">
    <li>
      <svg viewBox="0 0 20 20" fill="none" stroke="#fff" stroke-width="1.5"><circle cx="10" cy="10" r="8"/><ellipse cx="10" cy="10" rx="3.5" ry="8"/><path d="M2 10h16M3.5 6h13M3.5 14h13"/></svg>
      www.BrookvaleDental.com
    </li>
    <li>
      <svg viewBox="0 0 20 20" fill="none" stroke="#fff" stroke-width="1.5"><path d="M10 18s-6-6-6-10a6 6 0 0 1 12 0c0 4-6 10-6 10z"/><circle cx="10" cy="8" r="2.2"/></svg>
      42 Harbour Rd, Brookvale, VIC 3790
    </li>
    <li>
      <svg viewBox="0 0 20 20" fill="none" stroke="#fff" stroke-width="1.5"><path d="M5 2l3 4-2 2c1 2.5 3.5 5 6 6l2-2 4 3-2 3C9 18 2 11 2 4z"/></svg>
      (03) 5550 1827
    </li>
  </ul>

  <footer class="languages">
    <p class="languages-intro">The languages spoken at the clinic are:</p>
    <p class="languages-list">English, Hindi, Punjabi and Persian.</p>
  </footer>
</main>
</body>
</html>
```